Business Card Design for a Personal Trainer

I need a business card design for my job as a personal trainer. It should have a unique, modern and exclusive design. On the front there should be only my logo with my name and my job. 0162/3819204 Tobias Lendhart Wiesengrundweg 14 80417 Munich Germany The most important contact information is the web adress. it can be bigger than the rest, but its not necessary. The card should be 8,5cmx5,5cm big. Font: Roboto. Colors: black, white, gray, 56c1ff.

```html
<!DOCTYPE html>
<html lang="de">
<head>
<meta charset="utf-8">
<title>Tobias Lendhart – Personal Trainer Business Card</title>
<link rel="stylesheet" href="https://fonts.googleapis.com/css2?family=Roboto:wght@400&family=Work+Sans:wght@400;500&display=swap">
<style>
  :root {
    --backdrop: #e2e2e2;
    --card-white: #ffffff;
    --card-black: #050607;
    --ink: #1a1a1a;
    --ink-soft: #2b2b2b;
    --paper-text: #ffffff;
    --photo-light: #d9d9d9;
    --photo-dark: #3a3a3a;
  }
  * { margin: 0; padding: 0; box-sizing: border-box; }
  html, body {
    width: 1200px;
    height: 897px;
    overflow: hidden;
    background: var(--backdrop);
  }
  .canvas {
    position: relative;
    width: 1200px;
    height: 897px;
  }
  .card {
    position: absolute;
    left: 330px;
    width: 542px;
    height: 310px;
    overflow: hidden;
  }
  .card--front { top: 108px; background: var(--card-white); }
  .card--back { top: 479px; background: var(--card-black); }

  .brand-name {
    position: absolute;
    left: 27px;
    top: 28px;
    font-family: "Roboto", sans-serif;
    font-weight: 400;
    font-size: 23px;
    letter-spacing: 0.2px;
    color: var(--ink);
    white-space: nowrap;
  }

  .contact {
    position: absolute;
    left: 28px;
    top: 113px;
    font-family: "Work Sans", sans-serif;
    color: var(--ink-soft);
  }
  .contact__name {
    font-weight: 500;
    font-size: 17px;
    letter-spacing: 0.6px;
    line-height: 22px;
    color: var(--ink);
  }
  .contact__role {
    font-size: 13.5px;
    line-height: 18px;
    margin-bottom: 20px;
  }
  .contact__address {
    font-size: 13.5px;
    line-height: 19px;
    font-style: normal;
    margin-bottom: 19px;
  }
  .contact__list { list-style: none; }
  .contact__item {
    display: flex;
    align-items: center;
    gap: 6px;
    font-size: 13.5px;
    line-height: 19px;
  }
  .contact__icon { width: 9px; height: 9px; flex: none; }

  .portrait {
    position: absolute;
    left: 282px;
    top: 8px;
    width: 250px;
    height: 302px;
    background: radial-gradient(ellipse at 50% 30%, var(--photo-light) 0%, #8a8a8a 35%, var(--photo-dark) 75%, var(--card-white) 100%);
  }

  .back-brand {
    position: absolute;
    left: 0;
    right: 0;
    top: 90px;
    display: flex;
    flex-direction: column;
    align-items: center;
    gap: 22px;
  }
  .back-brand__mark {
    width: 40px;
    height: 40px;
    background: var(--paper-text);
  }
  .back-brand__name {
    font-family: "Roboto", sans-serif;
    font-weight: 400;
    font-size: 32px;
    letter-spacing: 0.3px;
    color: var(--paper-text);
    white-space: nowrap;
  }
</style>
</head>
<body>
<main class="canvas">
  <section class="card card--front">
    <div class="brand-name">TOBIAS LENDHART</div>

    <div class="contact">
      <div class="contact__name">TOBIAS LENDHART</div>
      <div class="contact__role">Personal Trainer</div>
      <address class="contact__address">
        Wiesengrundweg 14<br>
        80417 München
      </address>
      <ul class="contact__list">
        <li class="contact__item">
          <svg class="contact__icon" viewBox="0 0 10 10" aria-hidden="true"><path d="M2 0.8 L3.6 2.8 L2.9 3.8 C3.5 5.1 4.6 6.3 6 6.9 L7 6.2 L9.1 7.7 L8.2 9.2 C4.3 8.9 0.9 5.6 0.7 1.7 Z" fill="#2b2b2b"/></svg>
          <span>0162/3819204</span>
        </li>
        <li class="contact__item">
          <svg class="contact__icon" viewBox="0 0 10 10" aria-hidden="true"><rect x="0.8" y="2" width="8.4" height="6" fill="none" stroke="#2b2b2b" stroke-width="1.1"/><path d="M1 2.3 L5 5.4 L9 2.3" fill="none" stroke="#2b2b2b" stroke-width="1.1"/></svg>
          <span>t.lendhart@mailpost.de</span>
        </li>
        <li class="contact__item">
          <svg class="contact__icon" viewBox="0 0 10 10" aria-hidden="true"><circle cx="5" cy="5" r="4.2" fill="none" stroke="#2b2b2b" stroke-width="1"/><ellipse cx="5" cy="5" rx="1.8" ry="4.2" fill="none" stroke="#2b2b2b" stroke-width="0.8"/><path d="M0.8 5 H9.2" stroke="#2b2b2b" stroke-width="0.8"/></svg>
          <span>www.tobiaslendhart.de</span>
        </li>
      </ul>
    </div>

    <div class="portrait" role="img" aria-label="Black and white portrait photo of the trainer, arms crossed, wearing a dark athletic shirt"></div>
  </section>

  <section class="card card--back">
    <div class="back-brand">
      <div class="back-brand__mark" aria-hidden="true"></div>
      <div class="back-brand__name">TOBIAS LENDHART</div>
    </div>
  </section>
</main>
</body>
</html>
```